Business cards to launch an education platform

Hi,
I am looking at having new business cards designed.
I am a startup, developing a web platform for schools and university, the education world. It's an online assessment system.
I would like a card that looks classy, and that is using the colors and the font of my logo.

I have attached:
1) my logo
2) A business card that I have designed quickly so you can have all the information required in the card, but I really don't like it.
3) The font that I am using (Lato Regular) to design my web platform
4) Some screenshots of my web platform so you can have a look at the style that I have.

Target Market(s)

Major market: Education system: Schools and university
Minor markets: Business in general

Industry/Entity Type

Business

Contact Information for Business Card

Clara Fenwick
Director

M: 0437 518 902
E: clara.fenwick@amberLoomSystems.com.au

Requirements
Must have
• The colors of my logo

```html
<!DOCTYPE html>
<html lang="en">
<head>
<meta charset="utf-8">
<title>Amber Loom Systems – Business Cards</title>
<link href="https://fonts.googleapis.com/css2?family=Lato:wght@300;400;700&display=swap" rel="stylesheet">
<style>
  :root {
    --navy: #0d4a7f;
    --navy-deep: #0a3f6e;
    --sky: #29b6e8;
    --ink: #124a80;
    --grey-text: #4a4f55;
    --paper: #ffffff;
    --backdrop: #e9ebee;
  }
  * { margin: 0; padding: 0; box-sizing: border-box; }
  html, body {
    width: 1200px;
    height: 950px;
    overflow: hidden;
    background: var(--backdrop);
    font-family: "Lato", sans-serif;
  }
  .canvas {
    position: relative;
    width: 1200px;
    height: 950px;
  }
  .card {
    position: absolute;
    width: 620px;
    height: 378px;
    border-radius: 4px;
    box-shadow: 0 6px 18px rgba(0,0,0,0.18);
    overflow: hidden;
  }

  /* Back of card */
  .card-back {
    left: 90px;
    top: 80px;
    background: var(--navy);
    color: var(--paper);
  }
  .card-back .brand {
    position: absolute;
    left: 150px;
    top: 118px;
    display: flex;
    align-items: center;
    gap: 18px;
  }
  .brand-square {
    width: 74px;
    height: 74px;
    flex: none;
  }
  .card-back .brand-square { background: var(--paper); }
  .brand-name {
    font-weight: 400;
    font-size: 34px;
    line-height: 1.05;
    letter-spacing: 2px;
  }
  .card-back .brand-name { color: var(--paper); }
  .card-back .website {
    position: absolute;
    left: 0;
    right: 0;
    top: 292px;
    text-align: center;
    font-size: 15px;
    letter-spacing: 0.5px;
    color: var(--paper);
  }

  /* Front of card */
  .card-front {
    left: 490px;
    top: 492px;
    background: var(--paper);
  }
  .card-front .band {
    position: absolute;
    inset: 0;
    width: 620px;
    height: 378px;
  }
  .card-front .brand {
    position: absolute;
    left: 92px;
    top: 118px;
    display: flex;
    align-items: center;
    gap: 26px;
  }
  .card-front .brand-square {
    background: var(--sky);
    border: 3px solid var(--paper);
  }
  .card-front .brand-name { color: var(--ink); }
  .person {
    position: absolute;
    left: 262px;
    top: 228px;
  }
  .person-name {
    font-weight: 700;
    font-size: 20px;
    color: var(--ink);
    letter-spacing: 0.3px;
  }
  .person-role {
    font-size: 14px;
    color: var(--sky);
    margin-top: 2px;
    letter-spacing: 0.3px;
  }
  .contact-list {
    list-style: none;
    margin-top: 16px;
  }
  .contact-item {
    display: flex;
    align-items: center;
    gap: 9px;
    font-size: 14px;
    color: var(--grey-text);
    margin-bottom: 7px;
  }
  .contact-icon { width: 14px; height: 14px; flex: none; }
</style>
</head>
<body>
<main class="canvas">

  <section class="card card-back" aria-label="Business card back">
    <div class="brand">
      <span class="brand-square"></span>
      <span class="brand-name">AMBER LOOM<br>Systems</span>
    </div>
    <p class="website">www.amberLoomSystems.com.au</p>
  </section>

  <section class="card card-front" aria-label="Business card front">
    <svg class="band" viewBox="0 0 620 378" aria-hidden="true">
      <polygon points="0,0 118,0 245,378 0,378" fill="var(--navy-deep)"/>
      <polygon points="0,0 118,0 142,72 0,168" fill="var(--sky)"/>
    </svg>

    <div class="brand">
      <span class="brand-square"></span>
      <span class="brand-name">AMBER LOOM<br>Systems</span>
    </div>

    <div class="person">
      <h1 class="person-name">CLARA FENWICK</h1>
      <p class="person-role">DIRECTOR</p>
      <ul class="contact-list">
        <li class="contact-item">
          <svg class="contact-icon" viewBox="0 0 14 14" aria-hidden="true">
            <rect x="3.5" y="0.5" width="7" height="13" rx="1.3" fill="none" stroke="var(--ink)" stroke-width="1.4"/>
            <line x1="6" y1="11.2" x2="8" y2="11.2" stroke="var(--ink)" stroke-width="1.2"/>
          </svg>
          <span>0437 518 902</span>
        </li>
        <li class="contact-item">
          <svg class="contact-icon" viewBox="0 0 14 14" aria-hidden="true">
            <rect x="0.5" y="2.5" width="13" height="9" fill="var(--ink)"/>
            <polyline points="0.8,3 7,8 13.2,3" fill="none" stroke="var(--paper)" stroke-width="1.1"/>
          </svg>
          <span>clara.fenwick@amberLoomSystems.com.au</span>
        </li>
      </ul>
    </div>
  </section>

</main>
</body>
</html>
```